Employee Benefits and Insurance Consulting

We are an existing company with over 30 years experience but are changing our name. We would like a simple design with grey tones.

Industry/Entity Type

Insurance

Contact Information for Business Card

Marlow Benefits Consulting
Gerald P Hollins CEO
5172 Brackenridge Road
Fairbrook, TN 37990
gerald@marlowbenefits-example.com
865-412-5593 - O
865-247-3861 - C

```html
<!DOCTYPE html>
<html lang="en">
<head>
<meta charset="utf-8">
<title>Marlow Benefits Consulting – Business Card</title>
<link rel="stylesheet" href="https://fonts.googleapis.com/css2?family=Open+Sans:wght@400;600;700&display=swap">
<style>
  :root {
    --backdrop: #9a9a9a;
    --card-black: #060606;
    --panel-black: #151515;
    --teal: #1e9a8e;
    --grey: #8c8c8c;
    --white: #ffffff;
  }
  * { box-sizing: border-box; margin: 0; padding: 0; }
  html, body { width: 1200px; height: 900px; overflow: hidden; }
  body {
    background: var(--backdrop);
    font-family: "Open Sans", Arial, sans-serif;
    position: relative;
  }
  .card {
    position: absolute;
    left: 250px;
    width: 700px;
    height: 400px;
    background: var(--card-black);
    overflow: hidden;
    box-shadow: 0 6px 18px rgba(0,0,0,0.35);
  }
  .card--back { top: 35px; }
  .card--front { top: 465px; }

  /* back */
  .back-brand {
    position: absolute;
    top: 130px; left: 0; right: 0;
    text-align: center;
  }
  .brand-name {
    color: var(--teal);
    font-weight: 700;
    font-size: 30px;
    letter-spacing: 1px;
    text-transform: uppercase;
    display: inline-flex;
    align-items: center;
    gap: 12px;
    white-space: nowrap;
  }
  .brand-mark {
    width: 18px; height: 18px;
    background: var(--grey);
    display: inline-block;
    flex: none;
  }
  .back-stripe-grey { position: absolute; left: 0; right: 0; bottom: 52px; height: 10px; background: var(--grey); }
  .back-stripe-teal { position: absolute; left: 0; right: 0; bottom: 0; height: 52px; background: var(--teal); }

  /* front */
  .front-brand { position: absolute; top: 98px; left: 38px; }
  .front-brand .brand-name { font-size: 24px; }
  .brand-rule { margin-top: 10px; width: 330px; height: 1px; background: var(--grey); }

  .person { position: absolute; top: 62px; right: 38px; text-align: right; }
  .person-name {
    color: var(--teal); font-weight: 700; font-size: 21px;
    text-transform: uppercase; letter-spacing: 0.5px;
  }
  .person-title { color: var(--white); font-size: 15px; margin-top: 4px; }

  .contact-panel {
    position: absolute; left: 0; right: 0; top: 218px; height: 122px;
    background: var(--panel-black);
  }
  .address {
    position: absolute; top: 14px; left: 38px;
    color: var(--white); font-size: 15px; line-height: 1.45;
    font-style: normal;
    display: flex; gap: 8px;
  }
  .address svg { margin-top: 3px; flex: none; }
  .contact-list {
    position: absolute; right: 38px; bottom: 12px;
    list-style: none; color: var(--white); font-size: 16px; line-height: 1.55;
    text-align: right;
  }
  .contact-list li { display: flex; justify-content: flex-end; align-items: center; gap: 12px; }
  .contact-list svg { flex: none; }

  .front-stripe-white-1 { position: absolute; left: 0; right: 0; top: 340px; height: 10px; background: var(--white); }
  .front-stripe-teal-1 { position: absolute; left: 0; right: 0; top: 350px; height: 30px; background: var(--teal); }
  .front-stripe-white-2 { position: absolute; left: 0; right: 0; top: 380px; height: 6px; background: var(--white); }
  .front-stripe-teal-2 { position: absolute; left: 0; right: 0; top: 386px; height: 14px; background: var(--teal); }
</style>
</head>
<body>

<section class="card card--back" aria-label="Business card back">
  <div class="back-brand">
    <span class="brand-name"><span class="brand-mark"></span>Marlow Benefits Consulting</span>
  </div>
  <div class="back-stripe-grey"></div>
  <div class="back-stripe-teal"></div>
</section>

<section class="card card--front" aria-label="Business card front">
  <div class="front-brand">
    <span class="brand-name"><span class="brand-mark"></span>Marlow Benefits Consulting</span>
    <div class="brand-rule"></div>
  </div>

  <div class="person">
    <p class="person-name">Gerald P Hollins</p>
    <p class="person-title">CEO</p>
  </div>

  <div class="contact-panel">
    <address class="address">
      <svg width="11" height="15" viewBox="0 0 11 15" aria-hidden="true">
        <path d="M5.5 0C2.5 0 0 2.4 0 5.4 0 9.3 5.5 15 5.5 15S11 9.3 11 5.4C11 2.4 8.5 0 5.5 0zm0 7.6a2.2 2.2 0 1 1 0-4.4 2.2 2.2 0 0 1 0 4.4z" fill="var(--teal)"/>
      </svg>
      <span>5172 Brackenridge Road<br>Fairbrook, TN 37990</span>
    </address>

    <ul class="contact-list">
      <li>865-247-3861
        <svg width="14" height="14" viewBox="0 0 14 14" aria-hidden="true">
          <path d="M3 0.5l2.2 3-1.3 1.6c.8 1.8 2.2 3.2 4 4l1.6-1.3 3 2.2-1.1 2.5C6 12.3 1.7 8 1.2 2.1z" fill="var(--teal)"/>
        </svg>
      </li>
      <li>865-412-5593
        <svg width="14" height="14" viewBox="0 0 14 14" aria-hidden="true">
          <rect x="3" y="0.5" width="8" height="13" rx="1.5" fill="var(--teal)"/>
          <rect x="4.5" y="2.5" width="5" height="8" fill="var(--panel-black)"/>
        </svg>
      </li>
      <li>gerald@marlowbenefits-example.com
        <svg width="14" height="14" viewBox="0 0 14 14" aria-hidden="true">
          <rect x="0.5" y="3" width="13" height="9" fill="var(--teal)"/>
          <path d="M0.5 3L7 8l6.5-5" fill="none" stroke="var(--panel-black)" stroke-width="1.2"/>
        </svg>
      </li>
    </ul>
  </div>

  <div class="front-stripe-white-1"></div>
  <div class="front-stripe-teal-1"></div>
  <div class="front-stripe-white-2"></div>
  <div class="front-stripe-teal-2"></div>
</section>

</body>
</html>
```